Business Card Design Project

I require a business card with the following information on them for various different people;
name
m:
f:
e:
I have a logo already and will attached that. We are in the construction industry. I require something clean and simple but eye catching at the same time. You can use another colour with our logo if you like and you can style the logo as well if you wish. I am open.
Also it needs to be front and back design.
Industry/Entity Type
Construction
Requirements
Must have
- Logo, name, mobile, fax and email address.
Front and back design

```html
<!DOCTYPE html>
<html lang="en">
<head>
<meta charset="UTF-8">
<title>Stoneway Builders – Business Card Front and Back</title>
<link href="https://fonts.googleapis.com/css2?family=Open+Sans:wght@400;600;700&display=swap" rel="stylesheet">
<style>
  :root {
    --stage: #a9862c;
    --card-white: #ffffff;
    --card-edge: #d9d9d9;
    --green-light: #8ccb45;
    --green-mid: #6ab534;
    --green-deep: #4f9a22;
    --brand-green: #4b9b2c;
    --text-light: #ffffff;
  }
  * { margin: 0; padding: 0; box-sizing: border-box; }
  html, body { width: 1200px; height: 686px; overflow: hidden; }
  body {
    background: var(--stage);
    font-family: "Open Sans", Arial, sans-serif;
    position: relative;
  }
  .card {
    position: absolute;
    width: 510px;
    height: 291px;
    border-radius: 12px;
    background: radial-gradient(ellipse at 45% 40%, var(--card-white) 45%, var(--card-edge) 100%);
    box-shadow: 1px 2px 3px rgba(0,0,0,0.45);
    overflow: hidden;
  }
  .card--front { left: 67px; top: 116px; }
  .card--back { left: 621px; top: 303px; }

  .front-panels { position: absolute; left: 0; top: 0; width: 510px; height: 291px; }

  .holder-name {
    position: absolute;
    right: 18px;
    top: 86px;
    font-size: 17px;
    line-height: 24px;
    font-weight: 700;
    color: var(--text-light);
    white-space: nowrap;
  }
  .contact-list {
    position: absolute;
    right: 18px;
    top: 185px;
    list-style: none;
    text-align: right;
    color: var(--text-light);
    font-size: 12px;
    line-height: 20px;
  }
  .contact-list li { display: flex; justify-content: flex-end; align-items: center; gap: 5px; white-space: nowrap; }
  .contact-list svg { width: 12px; height: 10px; fill: var(--text-light); }

  .brand {
    position: absolute;
    display: flex;
    align-items: center;
    color: var(--brand-green);
    font-weight: 400;
    white-space: nowrap;
  }
  .brand__square { background: var(--brand-green); flex: none; }
  .brand--front { left: 25px; top: 192px; font-size: 24px; gap: 9px; }
  .brand--front .brand__square { width: 22px; height: 22px; }
  .brand--back { left: 70px; top: 118px; font-size: 39px; gap: 13px; }
  .brand--back .brand__square { width: 32px; height: 32px; }
</style>
</head>
<body>

<section class="card card--front" aria-label="Business card front">
  <svg class="front-panels" viewBox="0 0 510 291" aria-hidden="true">
    <defs>
      <linearGradient id="tabGreen" x1="0" y1="0" x2="0" y2="1">
        <stop offset="0" stop-color="var(--green-light)"/>
        <stop offset="1" stop-color="var(--green-mid)"/>
      </linearGradient>
      <linearGradient id="panelGreen" x1="0" y1="0" x2="0" y2="1">
        <stop offset="0" stop-color="var(--green-mid)"/>
        <stop offset="1" stop-color="var(--green-deep)"/>
      </linearGradient>
    </defs>
    <path class="name-tab" d="M510 20 L510 140 L338 140 Q327 140 334 132 L440 28 Q448 20 460 20 Z" fill="url(#tabGreen)"/>
    <path class="contact-panel" d="M510 150 L510 267 L330 267 Q319 267 319 256 L319 161 Q319 150 330 150 Z" fill="url(#panelGreen)"/>
  </svg>

  <p class="holder-name">Your Name</p>

  <ul class="contact-list">
    <li>123-456-7890
      <svg viewBox="0 0 12 10"><path d="M1 4 Q6 -1 11 4 L9 6 L8 4 Q6 3 4 4 L3 6 Z"/></svg>
    </li>
    <li>123-456-7890
      <svg viewBox="0 0 12 10"><rect x="3" y="0" width="6" height="3"/><rect x="0" y="4" width="12" height="6"/></svg>
    </li>
    <li>name@website.com
      <svg viewBox="0 0 12 10"><path d="M0 1 H12 V9 H0 Z M1 2 L6 6 L11 2 Z" fill-rule="evenodd"/></svg>
    </li>
  </ul>

  <div class="brand brand--front">
    <span class="brand__square"></span>
    <span class="brand__name">Stoneway Builders</span>
  </div>
</section>

<section class="card card--back" aria-label="Business card back">
  <div class="brand brand--back">
    <span class="brand__square"></span>
    <span class="brand__name">Stoneway Builders</span>
  </div>
</section>

</body>
</html>
```